I have a website called Okenta Holdings (okentaholdings.com) that I would like to have redesigned. Most of the content is already created, but I need a new design. You can also see my other website at brambleacres.com. I am open to a new logo or modifying the current logo if you have a good idea. Please feel free to use other images for the home page (and maybe some other locations) if you feel they provide a better look and feel to the website. I prefer a modern look.

Important: You do not have to use the images I've provided for the home page. Feel free to find your own stock photos. You don't have to pay for them unless I select your design.

1) Please use wix.com to make your changes so that I can edit it later.
2) I will need all the graphics files to be saved so I can dowload it for later.
3) I will be adding more content to the site later.
4) This site will likely be transferred over to brambleacres.com so if you make a logo please make one for Okenta Holdings and one for Bramble Acres.
5) You can use other images that you feel would help the look and feel of the website.

```html
<!DOCTYPE html>
<html lang="en">
<head>
<meta charset="utf-8">
<title>Okenta Holdings</title>
<link href="https://fonts.googleapis.com/css2?family=Rubik:wght@500;700;800&family=Roboto:wght@400;500;700&display=swap" rel="stylesheet">
<style>
:root{
  --navy:#0b2a4f;
  --navy-deep:#0d2b52;
  --sky:#5499d3;
  --sky-light:#eef5fb;
  --ink:#111;
  --body:#6b6b6b;
  --white:#fff;
  --link-active:#5aa1e0;
}
*{margin:0;padding:0;box-sizing:border-box}
html,body{width:1200px;height:3903px;overflow:hidden}
body{position:relative;background:var(--white);font-family:'Roboto',Arial,sans-serif;color:var(--ink)}
.abs{position:absolute}
.photo{position:absolute;display:block}

/* hero */
.hero{left:0;top:0;width:1200px;height:712px;
  background:linear-gradient(180deg,#4a5a78 0%,#9a7a62 22%,#d08a3e 36%,#7d6a5c 52%,#6a6e78 68%,#4d5a3e 85%,#2f3d24 100%)}
.brand{position:absolute;display:flex;align-items:center;gap:14px;color:var(--white);font-family:'Roboto',Arial,sans-serif;font-weight:400;font-size:32px;letter-spacing:-0.5px}
.brand-mark{width:40px;height:40px;border:3px solid var(--white)}
.nav{position:absolute;top:40px;right:114px;display:flex;gap:34px;font-size:15px;font-weight:500}
.nav a{color:var(--white);text-decoration:none}
.nav a.active{color:var(--link-active)}
.hero-title{left:110px;top:230px;width:600px;font-family:'Rubik',sans-serif;font-weight:700;font-size:39px;line-height:47px;color:var(--white)}
.hero-text{left:111px;top:388px;width:465px;font-size:13.5px;line-height:22px;font-weight:700;color:var(--white);text-align:justify}

/* section headings */
.h-section{font-family:'Rubik',sans-serif;font-weight:700;font-size:29px;letter-spacing:0.3px;color:var(--ink)}
.copy{font-size:14px;line-height:24px;color:var(--body);text-align:justify}
.btn{position:absolute;display:flex;align-items:center;justify-content:center;gap:10px;font-size:12.5px;font-weight:700;color:var(--white);border-radius:3px;letter-spacing:0.2px}
.btn svg{width:13px;height:13px}

.focus-list{left:677px;top:842px;list-style:none;font-family:'Rubik',sans-serif;font-weight:700;font-size:33px;line-height:65px}

/* why band */
.why{left:0;top:1195px;width:1200px;height:357px;background:var(--sky);color:var(--white)}
.why h2{position:absolute;top:88px;width:100%;text-align:center;font-family:'Rubik',sans-serif;font-weight:700;font-size:33px}
.stat{position:absolute;top:190px;width:260px;margin-left:-130px;text-align:center}
.stat b{display:block;font-family:'Rubik',sans-serif;font-weight:700;font-size:34px;line-height:40px}
.stat span{display:block;margin-top:8px;font-size:18px}

.center-title{left:0;width:1200px;text-align:center}
.play{position:absolute;left:50%;top:50%;width:48px;height:48px;margin:-24px 0 0 -24px}

.about{left:0;top:2104px;width:1200px;height:528px;background:var(--sky-light)}

/* footer */
.footer{left:0;top:3403px;width:1200px;height:500px;background:var(--navy-deep);color:var(--white)}
.sub-title{left:111px;top:114px;font-family:'Rubik',sans-serif;font-weight:700;font-size:25px;line-height:38px}
.field{position:absolute;width:211px;border-bottom:1px solid #6f86a6;font-size:13px;padding-bottom:12px}
.contact{left:488px;top:262px;font-size:16.5px;line-height:22px}
.contact .row{position:absolute;left:0;display:flex;white-space:nowrap}
.contact .k{width:64px;font-weight:700}
.contact .c{width:18px}
.foot-links{left:956px;top:258px;list-style:none;font-size:16.5px;line-height:38px}
.copyright{left:112px;top:362px;font-size:12.5px}
</style>
</head>
<body>

<!-- HERO -->
<div class="abs hero photo" role="img" aria-label="City skyline at sunset with trees in the foreground"></div>
<div class="brand" style="left:112px;top:28px">
  <span class="brand-mark"></span><span>Okenta Holdings</span>
</div>
<nav class="nav">
  <a class="active">Home</a><a>Strategy</a><a>About Us</a><a>Current Offerings</a><a>Contact</a>
</nav>
<h1 class="abs hero-title">Private Commercial Real Estate Investment and Development Firm</h1>
<p class="abs hero-text">Okenta Holdings is a private real estate firm that specializes in the procurement, development, management, and disposition of various commercial real estate asset types including multifamily, industrial, single-family, hospitality, self-storage, and flex.</p>

<!-- STRATEGY -->
<h2 class="abs h-section" style="left:112px;top:808px">STRATEGY</h2>
<p class="abs copy" style="left:113px;top:866px;width:464px">Bramble Acres evaluates opportunities with a two-pronged approach. First, the firm searches for development opportunities which are in growing metropolitan markets and possess a high barrier to entry. Second, the firm actively purses the acquisition of distressed or value-add assets which yield compelling cash-on-cash returns. The diverse background of the firm avails an opportunistic and entrepreneurial evaluation of each transaction.</p>
<div class="btn" style="left:113px;top:1059px;width:152px;height:48px;background:var(--navy)">LEARN MORE
  <svg viewBox="0 0 14 14"><circle cx="7" cy="7" r="7" fill="#fff"/><path d="M6 4l3 3-3 3" stroke="#0b2a4f" stroke-width="2" fill="none"/></svg></div>
<ul class="abs focus-list">
  <li>Investment Focus</li><li>Development</li><li>Acquisitions</li><li>Product Types</li>
</ul>

<!-- WHY CHOOSE US -->
<section class="abs why">
  <h2>WHY CHOOSE US</h2>
  <div class="stat" style="left:208px"><b>2017</b><span>Year Established</span></div>
  <div class="stat" style="left:449px"><b>DALLAS, TX</b><span>Headquarters</span></div>
  <div class="stat" style="left:727px"><b>$100MM+</b><span>Assets Under Management</span></div>
  <div class="stat" style="left:994px"><b>6</b><span>Current Projects</span></div>
</section>

<!-- VIDEOS -->
<h2 class="abs h-section center-title" style="top:1654px;font-size:33px">OUR VIDEOS</h2>
<div class="photo" style="left:111px;top:1741px;width:315px;height:256px;background:linear-gradient(135deg,#3d4658,#8a6a5a 50%,#2e3648)" role="img" aria-label="Aerial night view of an industrial site">
  <svg class="play" viewBox="0 0 48 48"><circle cx="24" cy="24" r="24" fill="#0b2a4f"/><path d="M19 15l14 9-14 9z" fill="#fff"/></svg></div>
<div class="photo" style="left:442px;top:1741px;width:316px;height:256px;background:linear-gradient(180deg,#cfdde8 0%,#8a7b6c 45%,#7a9a5a 80%,#a9b89a)" role="img" aria-label="Rendering of a modern apartment complex">
  <svg class="play" viewBox="0 0 48 48"><circle cx="24" cy="24" r="24" fill="#0b2a4f"/><path d="M19 15l14 9-14 9z" fill="#fff"/></svg></div>
<div class="photo" style="left:773px;top:1741px;width:315px;height:256px;background:linear-gradient(180deg,#c9d9e6 0%,#d8c8ae 40%,#6f8a55 75%,#9a9a94)" role="img" aria-label="Rendering of a residential street with townhomes">
  <svg class="play" viewBox="0 0 48 48"><circle cx="24" cy="24" r="24" fill="#0b2a4f"/><path d="M19 15l14 9-14 9z" fill="#fff"/></svg></div>

<!-- ABOUT -->
<section class="abs about"></section>
<h2 class="abs h-section" style="left:112px;top:2176px">ABOUT US</h2>
<p class="abs copy" style="left:113px;top:2234px;width:404px">Bramble Acres is a private real estate firm that specializes in the procurement, development, management, and disposition of various commercial real estate asset types including multifamily, industrial, single-family, hospitality, self-storage, and flex. The firm effectuates its strategy by utilizing long-standing relationships to ascertain acquisition and development opportunities within a specific target market. Bramble Acres is currently focused on acquisition and development opportunities in the southern portion of the United States.</p>
<div class="btn" style="left:113px;top:2504px;width:152px;height:49px;background:var(--sky)">LEARN MORE
  <svg viewBox="0 0 14 14"><circle cx="7" cy="7" r="7" fill="#fff"/><path d="M6 4l3 3-3 3" stroke="#5499d3" stroke-width="2" fill="none"/></svg></div>
<div class="photo" style="left:576px;top:2194px;width:252px;height:348px;background:linear-gradient(180deg,#4f8fd6 0%,#c9b89c 40%,#7fd0e0 70%,#e2e2de)" role="img" aria-label="Apartment pool deck with lounge chairs"></div>
<div class="photo" style="left:836px;top:2194px;width:252px;height:169px;background:linear-gradient(160deg,#6aa3dc 0%,#cbbfae 45%,#7a7470)" role="img" aria-label="Modern townhouse exterior"></div>
<div class="photo" style="left:836px;top:2373px;width:252px;height:169px;background:linear-gradient(180deg,#5f96d0 0%,#8a8d86 45%,#6c8a48 80%)" role="img" aria-label="Community entrance sign with landscaping"></div>

<!-- GALLERY -->
<h2 class="abs h-section center-title" style="top:2713px;font-size:29px">OUR GALLERY</h2>
<div class="photo" style="left:111px;top:2786px;width:315px;height:246px;background:linear-gradient(180deg,#e8e6e2,#b9b4ae 60%,#8a7a68)" role="img" aria-label="Bright apartment kitchen"></div>
<div class="photo" style="left:442px;top:2786px;width:316px;height:246px;background:linear-gradient(180deg,#7fb3e6 0%,#8a7565 50%,#5d5a58)" role="img" aria-label="Mid-rise mixed-use building"></div>
<div class="photo" style="left:773px;top:2786px;width:315px;height:246px;background:linear-gradient(180deg,#3d7ed0 0%,#d8d6d2 50%,#a07a5a)" role="img" aria-label="High-rise residential tower"></div>
<div class="photo" style="left:111px;top:3053px;width:315px;height:245px;background:linear-gradient(135deg,#24304a,#4a5a6a 50%,#5e6a3a)" role="img" aria-label="Modern home terrace at dusk"></div>
<div class="photo" style="left:442px;top:3053px;width:316px;height:245px;background:linear-gradient(180deg,#1f56b8 0%,#8a6e5a 55%,#4e4640)" role="img" aria-label="Hotel exterior at night"></div>
<div class="photo" style="left:773px;top:3053px;width:315px;height:245px;background:linear-gradient(180deg,#cfc8c0,#8a8278 55%,#b9a458)" role="img" aria-label="Living room with fireplace and chandelier"></div>

<!-- FOOTER -->
<footer class="abs footer">
  <h3 class="abs sub-title">STAY CONNECTED. LEARN FROM OUR<br>EXPERTS. SUBSCRIBE</h3>
  <div class="field" style="left:651px;top:90px">First Name</div>
  <div class="field" style="left:877px;top:90px">Last Name</div>
  <div class="field" style="left:651px;top:151px">Email</div>
  <div class="btn" style="left:877px;top:141px;width:211px;height:39px;background:var(--sky);border-radius:0">SUBSCRIBE NOW</div>

  <div class="brand" style="left:114px;top:262px"><span class="brand-mark"></span><span>Okenta Holdings</span></div>
  <p class="abs copyright">© 2022 Okenta Holdings. ALl Rights Reserved</p>

  <div class="abs contact">
    <div class="row" style="top:0"><span class="k">Address</span><span class="c">:</span><span>4470 Larkspur Ave. 5th Floor<br>Dallas, Texas 75219</span></div>
    <div class="row" style="top:68px"><span class="k">Email</span><span class="c">:</span><span>info@brambleacres.com</span></div>
    <div class="row" style="top:112px"><span class="k">Phone</span><span class="c">:</span><span>(214) 555-0187</span></div>
  </div>
  <ul class="abs foot-links">
    <li>Home</li><li>Strategy</li><li>About Us</li><li>Current Offerings</li><li>Contact</li>
  </ul>
</footer>

</body>
</html>
```